Creation of a Velmaro website

Velmaro is a company% 26 # 233; t% 26 # 233; consulting that accompanies Swiss companies or% 26 # 233; strang% 26 # 232; res in the d% 26 # 233; development of their business on the market% 26 # 233; Switzerland by providing strategic contacts (personalized contact program% 26 # 233; s) or market information% 26 # 233; (% 26 # 233; market research% 26 # 233;) and by providing administrative support (repr% 26 # 233; tax representation) or logistics (organization of% 26 # 233; v% 26 # 233; nement, assistance for participation% 26 # 224; fairs). Our customers are mainly European companies wishing to develop their business in Switzerland. N% 26 # 233; however, our services are% 26 # 233; also aimed at Swiss companies wishing to develop in other parts of Switzerland. Our site must therefore be% 26 # 234; capable of being translated into several languages. The services offered% 26 # 233; s by Velmaro may also% 26 # 233; also% 26 # 39;% 26 # 233; tender% 26 # 224; promoting tourism in Switzerland for countries or regions% 26 # 233; foreigners or% 26 # 224; the promotion of trade fairs or fairs with% 26 # 232; sd% 26 # 39; companies of the sectors concerned% 26 # 233; s. It is therefore n% 26 # 233; necessary to be able to add sub-headings of services which can% 26 # 234; be displayed% 26 # 233; es or hide% 26 # 233; es as required. We are 2 associates% 26 # 233; s, low% 26 # 233; s in the French-speaking parts (Neuch% 26 # 226; tel) and al% 26 # 233; manique (Zurich) of Switzerland.

Target Market(s)

Swiss or European companies wishing to develop their activities in Switzerland.

Coding

Coded - Design and coding required

Colors

Designer to choose colors to be used in the design.

Requirements
Must have
• A home page A section of% 26 # 233; writing the services offered% 26 # 233; es by Velmaro with the possibility% 26 # 233; d% 26 # 39; add sub-headings which can% 26 # 234; be displayed% 26 # 233; e or hidden% 26 # 233; e A page with the r% 26 # 233; f% 26 # 233; which can be displayed% 26 # 233; e or hidden% 26 # 233; e A page of% 26 # 233; writing l% 26 # 39;% 26 # 233; team A page with form contact, addresses and int card% 26 # 233; gr% 26 # 233; e The site must% 26 # 234; be low% 26 # 233; on a CMS allowing% 26 # 39;% 26 # 234; to be autonomous in modifying the website The possibility% 26 # 233; to be able to translate the site into several languages (FR, EN, DE, IT, NL, ...)

```html
<!DOCTYPE html>
<html lang="en">
<head>
<meta charset="utf-8">
<title>Velmaro – Business Development in Switzerland</title>
<link href="https://fonts.googleapis.com/css2?family=Exo+2:wght@600;700&family=Barlow:wght@400;500;600&display=swap" rel="stylesheet">
<style>
:root{
  --navy:#1b3049;
  --navy-deep:#142538;
  --ink:#1d2a38;
  --text:#3c4654;
  --muted:#6b7480;
  --white:#ffffff;
  --line:#e4e8ee;
  --hero-a:#0d2f4f;
  --hero-b:#2e7fa5;
}
*{margin:0;padding:0;box-sizing:border-box}
html,body{width:1200px;height:4040px;overflow:hidden;background:var(--white)}
body{position:relative;font-family:"Barlow",Arial,sans-serif;color:var(--text)}
.abs{position:absolute}
h1,h2,h3,.brand-name{font-family:"Exo 2","Barlow",sans-serif}

/* header */
.site-header{position:absolute;left:0;top:0;width:1200px;height:72px;background:var(--white);z-index:3}
.brand{position:absolute;display:flex;align-items:center;gap:14px}
.brand-mark{width:38px;height:38px;border-radius:8px;background:var(--navy)}
.brand-name{font-size:32px;font-weight:600;letter-spacing:3px;color:var(--navy)}
.main-nav{position:absolute;top:28px;left:482px;display:flex;font-size:13px;font-weight:500;color:var(--ink)}
.main-nav a{position:absolute;white-space:nowrap;text-decoration:none;color:inherit}
.lang{position:absolute;left:952px;top:18px;padding-left:20px;border-left:1px solid #cfd5dc;height:36px;display:flex;align-items:center;gap:6px;font-size:13px;font-weight:500;color:var(--ink)}
.lang i{width:14px;height:14px;border-radius:50%;background:#c8102e;display:block}

/* hero */
.hero{position:absolute;left:0;top:72px;width:1200px;height:670px;background:linear-gradient(120deg,var(--hero-a) 0%,#17496e 45%,var(--hero-b) 75%,#0f3554 100%)}
.hero-wave{position:absolute;left:0;top:0}
.hero-title{position:absolute;left:172px;top:137px;font-size:46px;line-height:53px;font-weight:700;color:var(--white);letter-spacing:.5px}
.hero-lead{position:absolute;left:172px;top:254px;width:330px;font-size:14.5px;line-height:22px;color:#e6eef5}
.hero-arrow{position:absolute;top:212px}

/* section heads */
.section-title{position:absolute;left:0;width:1200px;text-align:center;font-size:40px;font-weight:700;color:var(--navy)}
.section-lead{position:absolute;left:300px;width:600px;text-align:center;font-size:12.5px;line-height:22px;color:var(--text)}

/* services */
.service-card{position:absolute;top:929px;width:267px;height:358px;border-radius:44px;background:var(--white);box-shadow:0 4px 18px rgba(27,48,73,.14);text-align:center}
.service-card svg.icon{position:absolute;left:93px;top:44px}
.service-card h3{position:absolute;top:155px;width:100%;font-family:"Barlow",sans-serif;font-size:16px;font-weight:500;color:var(--ink)}
.service-card p{position:absolute;left:30px;top:192px;width:207px;font-size:12.5px;line-height:22px;color:var(--text)}
.round-btn{position:absolute;left:118px;top:294px;width:30px;height:30px;border:1.5px solid var(--ink);border-radius:50%}

/* about */
.about-back{position:absolute;left:172px;top:1381px;width:354px;height:384px;border-radius:60px 60px 0 60px;background:linear-gradient(160deg,#2d4660,#8b8f94 55%,#d9d6d0)}
.about-frame{position:absolute;left:270px;top:1549px;width:306px;height:313px;border-radius:60px 40px 40px 40px;background:var(--white)}
.about-photo{position:absolute;left:284px;top:1565px;width:292px;height:297px;border-radius:46px 30px 30px 30px;background:linear-gradient(150deg,#3e5264,#7d8b96 50%,#d6dde2)}
.about-tag{position:absolute;left:466px;top:1421px;width:350px;height:65px;background:var(--navy);border-radius:10px;color:var(--white);font-size:38px;font-weight:600;display:flex;align-items:center;justify-content:center}
.about-text{position:absolute;left:634px;top:1509px;width:392px;font-size:12.5px;line-height:23.2px;text-align:justify;color:var(--text)}
.btn-dark{position:absolute;left:634px;top:1767px;width:124px;height:44px;border-radius:8px;background:var(--navy);color:var(--white);font-size:14px;font-weight:600;display:flex;align-items:center;justify-content:center}

/* testimonials */
.testimonials{position:absolute;left:0;top:1947px;width:1200px;height:438px;background:var(--navy)}
.testimonials h2{position:absolute;left:172px;top:118px;font-family:"Barlow",sans-serif;font-size:31px;line-height:36px;font-weight:600;color:var(--white)}
.testimonials .lead{position:absolute;left:172px;top:210px;width:290px;font-size:14px;line-height:24px;color:#dde4ec}
.testimonials .all-link{position:absolute;left:172px;top:268px;font-size:15px;font-weight:600;color:var(--white);text-decoration:underline}
.quote-card{position:absolute;top:93px;height:252px;border-radius:8px;overflow:hidden;background:linear-gradient(90deg,#c9d1d8,#e8ecef 60%,#dfe5ea)}
.quote-person{position:absolute;left:50px;top:40px;width:140px;height:212px;background:linear-gradient(180deg,#7a858f,#28333f);border-radius:70px 70px 0 0}
.quote-text{position:absolute;left:250px;top:78px;width:190px;font-size:12.5px;font-style:italic;line-height:22px;color:#4a5562}
.quote-name{position:absolute;left:250px;top:174px;font-size:13px;font-weight:600;color:var(--ink)}
.play{position:absolute;left:33px;top:183px;width:42px;height:42px;border-radius:50%;background:var(--navy);border:2px solid var(--white)}

/* news */
.news-card{position:absolute;top:2609px;width:268px;height:397px;background:var(--white);box-shadow:0 4px 16px rgba(27,48,73,.12);text-align:center}
.news-card svg{position:absolute;left:0;top:0}
.news-card h3{position:absolute;top:204px;width:100%;font-family:"Barlow",sans-serif;font-size:21px;font-weight:600;color:var(--ink)}
.news-card p{position:absolute;left:22px;top:246px;width:224px;font-size:12.5px;line-height:23px;color:var(--text)}
.news-date{position:absolute;top:354px;width:100%;font-size:11.5px;font-weight:600;color:var(--ink);display:flex;justify-content:center;align-items:center;gap:6px}

/* contact */
.contact{position:absolute;left:0;top:3135px;width:1200px;height:557px}
.contact-panel{position:absolute;left:0;top:0;width:570px;height:557px;background:var(--navy)}
.contact-photo{position:absolute;left:570px;top:0;width:630px;height:557px;background:linear-gradient(120deg,#d9dee3,#f1f2f2 45%,#8a949e 85%,#4a5560)}
.contact h2{position:absolute;left:172px;top:60px;font-size:36px;font-weight:600;color:var(--white)}
.contact .lead{position:absolute;left:172px;top:124px;width:332px;font-size:12px;line-height:23px;color:#dbe2ea}
.field{position:absolute;left:172px;width:325px;border-bottom:1.5px solid #c7d0da;color:var(--white);font-size:12.5px}
.field span{position:absolute;left:0}
.field i{position:absolute;right:2px;width:10px;height:10px;border-radius:2px;background:#9aa7b5}
.btn-outline{position:absolute;left:172px;top:471px;width:96px;height:42px;border:2px solid var(--white);border-radius:8px;color:var(--white);font-size:14px;font-weight:600;display:flex;align-items:center;justify-content:center}

/* footer */
.site-footer{position:absolute;left:0;top:3692px;width:1200px;height:348px;background:var(--navy-deep);color:#d5dde6}
.footer-col{position:absolute;top:72px}
.footer-col h4{font-size:15px;font-weight:600;color:var(--white);margin-bottom:14px}
.footer-col li{list-style:none;font-size:11px;line-height:22.6px}
.contact-item{position:absolute;left:180px;display:flex;gap:16px;font-size:11px;line-height:19px}
.contact-item svg{flex:none}
.footer-brand{position:absolute;left:172px;top:292px}
.footer-brand .brand-mark{background:var(--white)}
.footer-brand .brand-name{color:var(--white)}
.copyright{position:absolute;left:580px;top:306px;font-size:10.5px}
.social{position:absolute;left:884px;top:304px;display:flex;gap:14px}
.social i{width:16px;height:16px;border-radius:50%;background:var(--white);display:block}
</style>
</head>
<body>

<header class="site-header">
  <div class="brand" style="left:172px;top:17px">
    <span class="brand-mark"></span><span class="brand-name">VELMARO</span>
  </div>
  <nav class="main-nav">
    <a style="left:0">HOME</a>
    <a style="left:72px">ABOUT</a>
    <a style="left:148px">SERVICES</a>
    <a style="left:241px">TEAM</a>
    <a style="left:314px">NEWS</a>
    <a style="left:388px">CONTACT</a>
  </nav>
  <div class="lang"><i></i>EN ▾</div>
</header>

<section class="hero">
  <div class="abs" role="img" aria-label="Business consultant touching a rising financial chart on a glowing data screen" style="inset:0"></div>
  <svg class="hero-wave" width="1200" height="670" viewBox="0 0 1200 670">
    <path d="M0 469 C300 520 700 570 950 628 C1080 660 1150 628 1200 540 L1200 670 L0 670 Z" fill="#ffffff"/>
    <path d="M0 469 C300 520 700 570 950 628 C1080 660 1150 628 1200 540" fill="none" stroke="#1b3049" stroke-width="6"/>
  </svg>
  <h1 class="hero-title">WELCOME TO<br>VELMARO</h1>
  <p class="hero-lead">Lorem ipsum dolor sit amet, consectetur adip iscing elit, sed do eiusmod tempor.</p>
  <svg class="hero-arrow" style="left:34px" width="30" height="60"><path d="M28 2 L2 30 L28 58" fill="none" stroke="#fff" stroke-width="1.5"/></svg>
  <svg class="hero-arrow" style="left:1124px" width="30" height="60"><path d="M2 2 L28 30 L2 58" fill="none" stroke="#fff" stroke-width="1.5"/></svg>
</section>

<h2 class="section-title" style="top:780px">OUR SERVICES</h2>
<p class="section-lead" style="top:842px">Lorem ipsum dolor sit amet, consectetur adipiscing elit, sed do eiusmod tempor incididunt ut labore et dolore magna aliqua. Ut enim ad minim veniam, quis nostrud exercitation.</p>

<article class="service-card" style="left:172px">
  <svg class="icon" width="80" height="82" viewBox="0 0 80 82" fill="none" stroke="#1d2a38" stroke-width="2.5">
    <path d="M8 6 H50 V76 H8 Z"/><path d="M16 70 V58 M24 70 V52 M32 70 V56 M40 70 V48"/>
    <circle cx="48" cy="34" r="16"/><path d="M59 46 L74 66"/><path d="M40 38 L46 30 L52 34 L58 26"/>
  </svg>
  <h3>MARKET RESEARCH</h3>
  <p>Lorem ipsum dolor sit ameconse cetur adipiscing elit, sed do eiusmod tem por incididunt ut laboreet lore magna aliquatenimeniam.</p>
  <span class="round-btn"></span>
</article>
<article class="service-card" style="left:466px">
  <svg class="icon" width="80" height="82" viewBox="0 0 80 82" fill="none" stroke="#1d2a38" stroke-width="2.5">
    <path d="M6 4 H52 V78 H6 Z"/><path d="M16 34 V24 M24 34 V14 M32 34 V20 M40 34 V26"/>
    <path d="M14 48 H32 M14 58 H30 M14 68 H28"/><circle cx="54" cy="56" r="16"/><path d="M47 63 L61 49"/>
  </svg>
  <h3>TAX REPRESENTATION</h3>
  <p>Lorem ipsum dolor sit ameconse cetur adipiscing elit, sed do eiusmod tem por incididunt ut laboreet lore magna aliquatenimeniam.</p>
  <span class="round-btn"></span>
</article>
<article class="service-card" style="left:759px">
  <svg class="icon" width="90" height="82" viewBox="0 0 90 82" fill="none" stroke="#1d2a38" stroke-width="2.5">
    <circle cx="42" cy="38" r="26"/><path d="M16 38 H68 M42 12 C30 24 30 52 42 64 M42 12 C54 24 54 52 42 64"/>
    <circle cx="14" cy="14" r="10"/><path d="M52 58 H80 V78 H52 Z M60 58 V68 H72 V58"/><path d="M4 70 H40 L34 78 H10 Z"/>
  </svg>
  <h3>LOGISTICS</h3>
  <p>Lorem ipsum dolor sit ameconse cetur adipiscing elit, sed do eiusmod tem por incididunt ut laboreet lore magna aliquatenimeniam.</p>
  <span class="round-btn"></span>
</article>

<div class="about-back" role="img" aria-label="Blurred office scene with colleagues at work"></div>
<div class="about-frame"></div>
<div class="about-photo" role="img" aria-label="Consultant in glasses reading a document"></div>
<h2 class="about-tag">ABOUT VELMARO</h2>
<p class="about-text">Lorem ipsum dolor sit amet, consectetur adipiscing elit, sed do eiusmod tempor incididunt ut labore et dolore magna aliqua. Ut enim ad minim veniam, quis nostrud exercitation ullamco laboris nisi ut aliquip exlot ea commodo consequat. Duis aute irure dolor in reprehenderiloret in volu ptate velit esse ciLorem ipsum dolor sit amet, consectetur adipiloresci ng elit, sed do eiusmod tempor incididunt ut labore et dolore magna aliqua. Ut enim ad minim veniam, quis nostrud exercitation ullamco laboris nisi ut aliquip ex ea commodo consequat. Duis aute irure dolor in reprehenderit in voluptate velit esse ciLorem ipsum dolor sit amet, cons ectetur adipiscing elit, sed do eiusmod tempor incididunt.</p>
<a class="btn-dark">READ MORE</a>

<section class="testimonials">
  <h2>WHAT OUR CLIENTS<br>ARE SAYING</h2>
  <p class="lead">Sed ut perspiciatis unde omnis iste natus sit volupt atem accusan tiumem.</p>
  <a class="all-link">View All Testimonials</a>
  <div class="quote-card" style="left:510px;width:474px">
    <div class="quote-person" role="img" aria-label="Smiling client with arms crossed"></div>
    <span class="play"><svg width="38" height="38"><path d="M15 12 L27 19 L15 26 Z" fill="#fff"/></svg></span>
    <p class="quote-text">“ Sed ut perspiciatis unde omnis Iste natus error sit voluptatem accusantium doloremque lauda ntium, totam rem aiaaqu ”</p>
    <p class="quote-name">Lena Hartwig</p>
  </div>
  <div class="quote-card" style="left:1020px;width:200px">
    <div class="quote-person" role="img" aria-label="Client portrait" style="opacity:.6"></div>
  </div>
</section>

<h2 class="section-title" style="top:2456px">LATEST NEWS</h2>
<p class="section-lead" style="top:2517px;left:340px;width:520px;font-size:14px;line-height:25px">Sed ut perspiciatis unde omnis iste natus error sit volupt atem accusantium doloremque laudantiuste natus error sit volupt m, totam rem aper.</p>

<article class="news-card" style="left:172px">
  <svg width="268" height="184" role="img" aria-label="Cardboard parcel on a conveyor belt"><defs><linearGradient id="n1" x1="0" y1="0" x2="1" y2="1"><stop offset="0" stop-color="#e9e2d6"/><stop offset=".5" stop-color="#c39a63"/><stop offset="1" stop-color="#3f5970"/></linearGradient></defs><path d="M0 0 H268 V150 C180 205 90 205 0 150 Z" fill="url(#n1)"/></svg>
  <h3>Sed utersiciatu</h3>
  <p>Sed ut perspiciatis unde omnisste natus error sit volupt atem accusanti um doloremque laudas error sit upt atem accusanti dolo launt.</p>
  <div class="news-date">▭ JAN 28 2020</div>
</article>
<article class="news-card" style="left:466px">
  <svg width="268" height="184" role="img" aria-label="Team reviewing charts at a desk"><defs><linearGradient id="n2" x1="0" y1="0" x2="1" y2="1"><stop offset="0" stop-color="#7b7568"/><stop offset=".5" stop-color="#d7dbe0"/><stop offset="1" stop-color="#30465c"/></linearGradient></defs><path d="M0 0 H268 V150 C180 205 90 205 0 150 Z" fill="url(#n2)"/></svg>
  <h3>Sed utersiciatu</h3>
  <p>Sed ut perspiciatis unde omnisste natus error sit volupt atem accusanti um doloremque laudas error sit upt atem accusanti dolo launt.</p>
  <div class="news-date">▭ JAN 28 2020</div>
</article>
<article class="news-card" style="left:758px">
  <svg width="268" height="184" role="img" aria-label="Laptop showing financial dashboards"><defs><linearGradient id="n3" x1="0" y1="0" x2="1" y2="1"><stop offset="0" stop-color="#d4d8dc"/><stop offset=".5" stop-color="#3d6f9a"/><stop offset="1" stop-color="#1f2a35"/></linearGradient></defs><path d="M0 0 H268 V150 C180 205 90 205 0 150 Z" fill="url(#n3)"/></svg>
  <h3>Sed utersiciatu</h3>
  <p>Sed ut perspiciatis unde omnisste natus error sit volupt atem accusanti um doloremque laudas error sit upt atem accusanti dolo launt.</p>
  <div class="news-date">▭ JAN 28 2020</div>
</article>

<section class="contact">
  <div class="contact-panel"></div>
  <div class="contact-photo" role="img" aria-label="Smiling businesswoman seated in a bright office with colleagues behind"></div>
  <h2>CONTACT US</h2>
  <p class="lead">Lorem ipsum dolor sit amet, consectetur adipiscing elit, sed do eiusmod tempor incididunt ut labore et dolore magna aliqua. Ut enim ad minim veniam, quis nostru.</p>
  <div class="field" style="top:229px;height:26px"><span>Name:</span><i style="top:3px;border-radius:50%"></i></div>
  <div class="field" style="top:277px;height:26px"><span>Email:</span><i style="top:3px"></i></div>
  <div class="field" style="top:327px;height:26px"><span>Phone:</span><i style="top:3px"></i></div>
  <div class="field" style="top:379px;height:70px"><span>Subject</span><i style="top:3px"></i></div>
  <a class="btn-outline">SUBMIT</a>
</section>

<footer class="site-footer">
  <div class="footer-col" style="left:182px"><h4>Contact</h4></div>
  <div class="contact-item" style="top:110px"><svg width="18" height="22" viewBox="0 0 18 22" fill="none" stroke="#d5dde6" stroke-width="1.4"><path d="M9 21 C3 13 2 10 2 8 A7 7 0 0 1 16 8 C16 10 15 13 9 21 Z"/><circle cx="9" cy="8" r="2.5"/></svg><span>14 Rue des Tilleuls,<br>Neuchâtel 2000</span></div>
  <div class="contact-item" style="top:162px"><svg width="18" height="20" viewBox="0 0 18 20" fill="none" stroke="#d5dde6" stroke-width="1.4"><path d="M3 2 L7 2 L8 7 L5 9 C6 12 8 14 11 15 L13 12 L17 13 L17 17 C10 18 2 11 3 2 Z"/></svg><span>+41 32 555 01 20<br>+41 44 555 07 36</span></div>
  <div class="contact-item" style="top:214px"><svg width="20" height="16" viewBox="0 0 20 16" fill="none" stroke="#d5dde6" stroke-width="1.4"><rect x="1" y="2" width="18" height="12"/><path d="M1 2 L10 9 L19 2"/></svg><span>hello@velmaro-consult.ch<br>partners@velmaro-consult.ch</span></div>
  <div class="footer-col" style="left:449px"><h4>About Us</h4><ul><li>Lorem ipsum dolo</li><li>Consectetur adipiscing elit.</li><li>Fusce eget leo tincid</li><li>Donec consequat</li><li>Praesent elementum</li><li>Jmauris posueret</li></ul></div>
  <div class="footer-col" style="left:679px"><h4>Information</h4><ul><li>Lorem ipsum dolo</li><li>Consectetur adipiscing elit.</li><li>Fusce eec consequat</li><li>Praesent elementum</li><li>Jmauris posueret</li><li>Aenean a ex eu lectu</li></ul></div>
  <div class="footer-col" style="left:891px"><h4>Other Links</h4><ul><li>Lorem ipsum dolo</li><li>Consecteturiscing elit.</li><li>Fusce eget leo tincid</li><li>Donec consequat</li><li>Praesent elementum</li><li>Aenean a ex eu lectu</li></ul></div>
  <div class="brand footer-brand"><span class="brand-mark"></span><span class="brand-name">VELMARO</span></div>
  <p class="copyright">Copyright 2020. All Rights Reserved</p>
  <div class="social"><i></i><i></i><i></i><i></i><i></i></div>
</footer>

</body>
</html>
```